24 Super Fantastic Banners 4 campaigns

I need 4 campaigns to have banners made, 6 banner sizes each so 24 total banners. Here are the landing pages with the messaging.

http://www.nearbyshopratings.example/Sandy-UT/Pellworth-Medical-48213.html

http://www.nearbyshopratings.example/Varnell-Law-Group-48212.html

http://www.nearbyshopratings.example/Dulvane-48211.html

http://www.nearbyshopratings.example/Kelpwise-com-48210.html

Need to get done asap. Much more work can be following right after. Here are the sizes

Sorry fix a typo. These sizes:

300 X 50
300x250
320 X50
216 X36
168 X 28
120 X 20

Medical

Requirements
Must have
• Must have phone number in the display for call to action

```html
<!DOCTYPE html>
<html lang="en">
<head>
<meta charset="utf-8">
<title>Pellworth Medical – Banner Set</title>
<link href="https://fonts.googleapis.com/css2?family=Arimo:wght@400;700&display=swap" rel="stylesheet">
<style>
  :root {
    --stage-light: #b3b1b1;
    --stage-dark: #9a9797;
    --brand-blue: #0d3f6e;
    --brand-blue-deep: #082c52;
    --headline-orange: #f26a10;
    --cta-green: #b8e630;
    --cta-green-dark: #7fb80e;
    --ink: #111820;
    --paper: #ffffff;
    --photo-light: #e7c7ad;
    --photo-dark: #9c7458;
    --product-light: #d7dde3;
    --product-dark: #8d98a4;
  }
  * { box-sizing: border-box; margin: 0; padding: 0; }
  html, body { width: 969px; height: 1200px; overflow: hidden; }
  body {
    position: relative;
    font-family: "Arimo", Arial, sans-serif;
    background: radial-gradient(ellipse at 50% 30%, var(--stage-light), var(--stage-dark));
  }

  /* ---------- horizontal banners ---------- */
  .banner {
    position: absolute;
    overflow: hidden;
    background: var(--brand-blue);
    box-shadow: 0 1px 3px rgba(0,0,0,.25);
  }
  .banner .photo {
    position: absolute; top: 0; left: 24%; width: 30%; height: 100%;
    background: linear-gradient(100deg, var(--photo-dark), var(--photo-light) 45%, var(--photo-dark));
  }
  .banner .panel { position: absolute; inset: 0; width: 100%; height: 100%; }
  .banner .brand-name {
    position: absolute; left: 3%; top: 50%; transform: translateY(-50%);
    color: var(--paper); font-weight: 700; font-size: 1.55em; line-height: 1.15;
    text-transform: uppercase; letter-spacing: .02em;
  }
  .banner .headline {
    position: absolute; left: 53%; top: 8%;
    color: var(--headline-orange); font-weight: 700; font-size: 1.7em; white-space: nowrap;
  }
  .banner .phone {
    position: absolute; left: 57%; bottom: 10%; height: 36%; padding: 0 .5em;
    display: flex; align-items: center;
    background: linear-gradient(180deg, var(--cta-green), var(--cta-green-dark));
    border-radius: .35em;
    color: var(--ink); font-weight: 700; font-size: 1.9em; white-space: nowrap;
  }
  .banner .phone span { font-size: .9em; }
  .banner .product {
    position: absolute; right: 3%; bottom: 8%; width: 11%; height: 52%;
    background: linear-gradient(160deg, var(--product-light), var(--product-dark));
    border-radius: 2px;
  }

  .size-120 { left: 425px; top: 70px;  width: 256px; height: 41px;  font-size: 4.2px; }
  .size-168 { left: 374px; top: 137px; width: 333px; height: 59px;  font-size: 5.9px; }
  .size-216 { left: 305px; top: 222px; width: 461px; height: 77px;  font-size: 7.7px; }
  .size-300 { left: 196px; top: 331px; width: 641px; height: 107px; font-size: 10.7px; }
  .size-320 { left: 175px; top: 468px; width: 683px; height: 108px; font-size: 10.8px; }

  /* ---------- medium rectangle ---------- */
  .rectangle {
    position: absolute; left: 196px; top: 602px; width: 641px; height: 532px;
    overflow: hidden; background: var(--paper);
    box-shadow: 0 1px 3px rgba(0,0,0,.25);
  }
  .rectangle .photo {
    position: absolute; top: 0; right: 0; width: 308px; height: 230px;
    background: linear-gradient(100deg, var(--photo-dark), var(--photo-light) 45%, var(--photo-dark));
  }
  .rectangle .panel { position: absolute; left: 0; top: 0; width: 641px; height: 260px; }
  .rectangle .brand-name {
    position: absolute; left: 22px; top: 30px;
    color: var(--paper); font-weight: 700; font-size: 40px; line-height: 1.3;
    text-transform: uppercase; letter-spacing: .02em;
  }
  .rectangle .headline {
    position: absolute; left: 20px; top: 226px;
    color: var(--headline-orange); font-weight: 700; font-size: 40px; white-space: nowrap;
  }
  .rectangle .supply-list {
    position: absolute; left: 36px; top: 286px; width: 580px;
    display: grid; grid-template-columns: 320px 1fr; row-gap: 2px;
    list-style: none; color: var(--ink); font-weight: 700; font-size: 25px; line-height: 1.25;
  }
  .rectangle .supply-list li { position: relative; padding-left: 24px; }
  .rectangle .supply-list li::before {
    content: ""; position: absolute; left: 0; top: 10px; width: 9px; height: 9px;
    background: var(--brand-blue);
  }
  .rectangle .phone {
    position: absolute; left: 62px; top: 432px; width: 376px; height: 78px;
    display: flex; align-items: center; justify-content: center;
    background: linear-gradient(180deg, var(--cta-green), var(--cta-green-dark));
    border-radius: 12px;
    color: var(--ink); font-weight: 700; font-size: 46px; white-space: nowrap;
  }
  .rectangle .product {
    position: absolute; left: 452px; top: 392px; width: 168px; height: 130px;
    background: linear-gradient(160deg, var(--product-light), var(--product-dark));
    border-radius: 4px;
  }
</style>
</head>
<body>

  <div class="banner size-120">
    <div class="photo" role="img" aria-label="Photo of a smiling couple"></div>
    <svg class="panel" viewBox="0 0 100 100" preserveAspectRatio="none" aria-hidden="true">
      <path d="M49 0 H100 V100 H43 C49 70 50 30 49 0 Z" fill="var(--paper)"/>
      <path d="M49 0 C50 30 49 70 43 100" fill="none" stroke="var(--brand-blue)" stroke-width="3" vector-effect="non-scaling-stroke"/>
    </svg>
    <div class="brand-name">Pellworth<br>Medical</div>
    <div class="headline">Diabetic Supplies Made Easy</div>
    <div class="phone"><span>(555) 014-2876</span></div>
    <div class="product" role="img" aria-label="Glucose meter kit box"></div>
  </div>

  <div class="banner size-168">
    <div class="photo" role="img" aria-label="Photo of a smiling couple"></div>
    <svg class="panel" viewBox="0 0 100 100" preserveAspectRatio="none" aria-hidden="true">
      <path d="M49 0 H100 V100 H43 C49 70 50 30 49 0 Z" fill="var(--paper)"/>
      <path d="M49 0 C50 30 49 70 43 100" fill="none" stroke="var(--brand-blue)" stroke-width="4" vector-effect="non-scaling-stroke"/>
    </svg>
    <div class="brand-name">Pellworth<br>Medical</div>
    <div class="headline">Diabetic Supplies Made Easy</div>
    <div class="phone"><span>(555) 014-2876</span></div>
    <div class="product" role="img" aria-label="Glucose meter kit box"></div>
  </div>

  <div class="banner size-216">
    <div class="photo" role="img" aria-label="Photo of a smiling couple"></div>
    <svg class="panel" viewBox="0 0 100 100" preserveAspectRatio="none" aria-hidden="true">
      <path d="M49 0 H100 V100 H43 C49 70 50 30 49 0 Z" fill="var(--paper)"/>
      <path d="M49 0 C50 30 49 70 43 100" fill="none" stroke="var(--brand-blue)" stroke-width="5" vector-effect="non-scaling-stroke"/>
    </svg>
    <div class="brand-name">Pellworth<br>Medical</div>
    <div class="headline">Diabetic Supplies Made Easy</div>
    <div class="phone"><span>(555) 014-2876</span></div>
    <div class="product" role="img" aria-label="Glucose meter kit box"></div>
  </div>

  <div class="banner size-300">
    <div class="photo" role="img" aria-label="Photo of a smiling couple"></div>
    <svg class="panel" viewBox="0 0 100 100" preserveAspectRatio="none" aria-hidden="true">
      <path d="M49 0 H100 V100 H43 C49 70 50 30 49 0 Z" fill="var(--paper)"/>
      <path d="M49 0 C50 30 49 70 43 100" fill="none" stroke="var(--brand-blue)" stroke-width="7" vector-effect="non-scaling-stroke"/>
    </svg>
    <div class="brand-name">Pellworth<br>Medical</div>
    <div class="headline">Diabetic Supplies Made Easy</div>
    <div class="phone"><span>(555) 014-2876</span></div>
    <div class="product" role="img" aria-label="Glucose meter kit box"></div>
  </div>

  <div class="banner size-320">
    <div class="photo" role="img" aria-label="Photo of a smiling couple"></div>
    <svg class="panel" viewBox="0 0 100 100" preserveAspectRatio="none" aria-hidden="true">
      <path d="M49 0 H100 V100 H43 C49 70 50 30 49 0 Z" fill="var(--paper)"/>
      <path d="M49 0 C50 30 49 70 43 100" fill="none" stroke="var(--brand-blue)" stroke-width="7" vector-effect="non-scaling-stroke"/>
    </svg>
    <div class="brand-name">Pellworth<br>Medical</div>
    <div class="headline">Diabetic Supplies Made Easy</div>
    <div class="phone"><span>(555) 014-2876</span></div>
    <div class="product" role="img" aria-label="Glucose meter kit box"></div>
  </div>

  <div class="rectangle">
    <div class="photo" role="img" aria-label="Photo of a smiling couple"></div>
    <svg class="panel" viewBox="0 0 641 260" aria-hidden="true">
      <path d="M0 0 H336 C322 60 326 120 350 175 L0 175 Z" fill="var(--brand-blue)"/>
      <path d="M0 175 H350 C400 215 500 225 641 170 V260 H0 Z" fill="var(--paper)"/>
      <path d="M0 160 C150 175 250 240 420 225 C520 215 590 190 641 160 V175 C590 205 520 230 420 238 C250 250 150 190 0 178 Z" fill="var(--brand-blue-deep)"/>
    </svg>
    <div class="brand-name">Pellworth<br>Medical</div>
    <div class="headline">Diabetic Supplies Made Easy</div>
    <ul class="supply-list">
      <li>Syringes</li>
      <li>Testing Supplies</li>
      <li>Testing Strips</li>
      <li>Glucose Meters</li>
      <li>Lancets and<br>Lancing Devices</li>
      <li>And More</li>
    </ul>
    <div class="phone">(555) 014-2876</div>
    <div class="product" role="img" aria-label="Glucose meter kit box and meter"></div>
  </div>

</body>
</html>
```